Kestrel Bathrooms Facelift. Moving the business in to the next professional level.

I'm currently revamping my bathroom renovation business. Part of this revamp includes our marketing strategy to better position ourselves as a professional business. As the name suggests, we primarily do bathroom renovations of all shapes, sizes and budgets. I'd like a business card design that is simple, yet displays our company as sophisticated.
What I'd like is to have a card that incorporates the following elements;
- Orange set as the primary colour and Charcoal/Grey as a complement colour. The card can also include white and/or black.
- I'd like a hexagon pattern within the charcoal/grey (In gloss perhaps to break it up a bit)
- I only want the Kestrel Bathrooms logo on the front of the card
- Back of the card would include contact details
- The bottom edges of the card would be rounded off
- I've attached the company name. I'd like to keep kestrel as it is. Bathrooms can be modified

```html
<!DOCTYPE html>
<html lang="en">
<head>
<meta charset="utf-8">
<title>Kestrel Bathrooms – Business Card</title>
<link href="https://fonts.googleapis.com/css2?family=Open+Sans:wght@400;600&display=swap" rel="stylesheet">
<style>
  :root {
    --backdrop: #7a5c3e;
    --card-white: #f7f7f7;
    --card-white-edge: #e6e6e6;
    --card-grey-light: #e9e9e9;
    --card-grey-dark: #a9a9a9;
    --ink: #1d1d1d;
    --ink-soft: #2e2e2e;
    --orange: #f2a42b;
    --rule: #3a3a3a;
  }
  * { margin: 0; padding: 0; box-sizing: border-box; }
  html, body {
    width: 1200px; height: 885px; overflow: hidden;
    background: var(--backdrop);
    font-family: "Open Sans", sans-serif;
  }
  .canvas { position: relative; width: 1200px; height: 885px; }

  .card {
    position: absolute; top: 287px;
    width: 540px; height: 310px;
    border-radius: 18px;
    box-shadow: 0 14px 30px rgba(0,0,0,0.35);
    overflow: hidden;
  }
  .card--front {
    left: 40px;
    background: linear-gradient(135deg, var(--card-white-edge) 0%, var(--card-white) 45%, #ffffff 70%, var(--card-white-edge) 100%);
  }
  .card--back {
    left: 620px;
    background: radial-gradient(ellipse at 40% 35%, var(--card-grey-light) 0%, #cfcfcf 55%, var(--card-grey-dark) 100%);
  }

  /* company name: single line, one weight, one colour */
  .company-name {
    position: absolute;
    color: var(--ink);
    font-weight: 400;
    line-height: 1;
    white-space: nowrap;
  }
  .card--front .company-name { left: 34px; top: 60px; font-size: 28px; }
  .card--back .company-name {
    left: 0; right: 0; top: 132px;
    text-align: center; font-size: 44px;
  }

  /* front details */
  .person { position: absolute; right: 34px; top: 34px; text-align: right; }
  .person__name { color: var(--orange); font-weight: 600; font-size: 22px; }
  .person__role { color: var(--ink-soft); font-size: 13px; margin-top: 2px; }
  .divider {
    position: absolute; left: 34px; right: 160px; top: 150px;
    height: 1px; background: var(--rule);
  }
  .contacts { position: absolute; left: 34px; top: 180px; list-style: none; }
  .contacts__item {
    display: flex; align-items: center; gap: 10px;
    font-size: 15px; color: var(--ink); height: 24px;
  }
  .contacts__icon { width: 16px; height: 16px; flex: none; }
  .address {
    position: absolute; right: 34px; bottom: 36px; text-align: right;
    font-size: 14px; line-height: 1.4; color: var(--ink); font-style: normal;
  }
</style>
</head>
<body>
<main class="canvas">

  <section class="card card--front" aria-label="Business card front">
    <p class="company-name">Kestrel Bathrooms</p>

    <div class="person">
      <p class="person__name">Employee Name</p>
      <p class="person__role">Owner</p>
    </div>

    <div class="divider"></div>

    <ul class="contacts">
      <li class="contacts__item">
        <svg class="contacts__icon" viewBox="0 0 16 16" aria-hidden="true">
          <rect width="16" height="16" rx="2" fill="var(--orange)"/>
          <path d="M5 3.5h2l1 2.5-1.3 1a5 5 0 0 0 2.3 2.3l1-1.3 2.5 1v2a1 1 0 0 1-1 1A8 8 0 0 1 4 4.5a1 1 0 0 1 1-1z" fill="#fff"/>
        </svg>
        000-000-0000
      </li>
      <li class="contacts__item">
        <svg class="contacts__icon" viewBox="0 0 16 16" aria-hidden="true">
          <rect width="16" height="16" rx="2" fill="var(--orange)"/>
          <circle cx="8" cy="8" r="4.5" fill="none" stroke="#fff" stroke-width="1"/>
          <ellipse cx="8" cy="8" rx="2" ry="4.5" fill="none" stroke="#fff" stroke-width="1"/>
          <line x1="3.5" y1="8" x2="12.5" y2="8" stroke="#fff" stroke-width="1"/>
        </svg>
        www.yourweb.com
      </li>
      <li class="contacts__item">
        <svg class="contacts__icon" viewBox="0 0 16 16" aria-hidden="true">
          <rect width="16" height="16" rx="2" fill="var(--orange)"/>
          <rect x="3" y="4.5" width="10" height="7" fill="none" stroke="#fff" stroke-width="1"/>
          <path d="M3 4.5l5 4 5-4" fill="none" stroke="#fff" stroke-width="1"/>
        </svg>
        You@youremail.com
      </li>
    </ul>

    <address class="address">
      Your Adress Inc 2nd Lane<br>Ave Edison, NJ 00000
    </address>
  </section>

  <section class="card card--back" aria-label="Business card back">
    <p class="company-name">Kestrel Bathrooms</p>
  </section>

</main>
</body>
</html>
```